** Wanted ** Wordpress web design for scaffolding rental and construction company

We need a website design and must be functional to show a basic overview of what our company offers as a service. We have a domain name and a logo but we need web design. This web site should have another scaffolding rental page for construction and renovation as well as a quote section where customers can enter their personal information and also upload photos. The site% 26quot; www.brindlework.com% 26quot; should be intuitive, clear and classy ... The logo must be found on the site in several ways.

Target Market(s)

Professional and no professional

Coding

Coded - Design and coding required

Number of Pages Required

3 page

Font styles to use
Serif
Sans Serif
Decorative
Script

Requirements
Must have
• Our logo
Nice to have
• Slogan:% 26quot; The height% 26 # 224; port% 26 # 233; e hand% 26quot;

```html
<!DOCTYPE html>
<html lang="en">
<head>
<meta charset="utf-8">
<title>Brindlework – Scaffolding &amp; Construction</title>
<link href="https://fonts.googleapis.com/css2?family=Black+Ops+One&family=Roboto:wght@300;400;500;700&family=PT+Serif:ital,wght@0,400;0,700;1,400&display=swap" rel="stylesheet">
<style>
:root{
  --orange:#f28a1c;
  --orange-deep:#e8700c;
  --dark:#2e2e30;
  --darker:#1f1f21;
  --ink:#222;
  --muted:#666;
  --white:#fff;
  --sky:#9fb6cc;
  --steel:#6f7478;
  --timber:#b8773a;
  --vest:#c9d13a;
}
*{margin:0;padding:0;box-sizing:border-box}
html,body{width:1200px;height:4984px;overflow:hidden}
body{position:relative;background:var(--white);font-family:'PT Serif',serif;color:var(--ink)}
.abs{position:absolute}
.photo{position:absolute;display:block}

/* hero */
.hero{position:absolute;left:0;top:0;width:1200px;height:700px}
.hero-photo{left:0;top:0;width:1200px;height:640px;
  background:
    radial-gradient(ellipse 380px 220px at 580px 500px,rgba(214,170,40,.75),transparent 70%),
    radial-gradient(ellipse 420px 260px at 980px 420px,rgba(236,160,70,.55),transparent 70%),
    radial-gradient(ellipse 500px 200px at 200px 520px,rgba(120,110,96,.6),transparent 70%),
    linear-gradient(180deg,#3a3c40 0%,#55524c 35%,#7a6a52 62%,#5c4c38 85%,#3e342a 100%)}
.hero-shade{left:0;top:0;width:1200px;height:640px;background:linear-gradient(180deg,rgba(20,20,22,.45),rgba(20,20,22,.15) 60%,rgba(20,20,22,.3))}
.topbar-phone{left:78px;top:18px;display:flex;align-items:center;gap:20px;color:var(--white);font:400 15px 'Roboto',sans-serif}
.phone-badge{width:44px;height:36px}
.btn{position:absolute;display:flex;align-items:center;justify-content:center;background:var(--orange);color:var(--white);font:500 15px 'Roboto',sans-serif;letter-spacing:.5px;clip-path:polygon(8% 0,92% 0,100% 50%,92% 100%,8% 100%,0 50%)}
.quote-btn{left:977px;top:17px;width:141px;height:39px;font-size:14px}
.nav{top:92px;font:400 13px 'PT Serif',serif;color:var(--white);letter-spacing:.3px}
.nav a{position:absolute;color:var(--white);text-decoration:none;white-space:nowrap}
.nav a.active{color:var(--orange)}
.nav-rule{top:72px;height:1px;background:rgba(255,255,255,.35)}
.nav-divider{top:28px;width:1px;height:96px;background:rgba(255,255,255,.3)}
.brand{left:511px;top:81px;width:174px;height:37px;border:3px solid var(--orange);display:flex;align-items:center;justify-content:center;gap:8px;font:700 15px 'Roboto',sans-serif;color:var(--orange);letter-spacing:1px}
.brand-dot{width:9px;height:9px;background:var(--orange)}
.hero-title{left:0;top:258px;width:1200px;text-align:center;font:400 60px 'Black Ops One',sans-serif;color:var(--white);letter-spacing:3px;text-shadow:0 2px 6px rgba(0,0,0,.4)}
.hero-sub{left:0;top:344px;width:1200px;text-align:center;font:italic 700 18px/31px 'PT Serif',serif;color:var(--white);text-shadow:0 1px 3px rgba(0,0,0,.4)}
.contact-btn{left:522px;top:435px;width:155px;height:47px;font-size:15px}
.hero-band{left:0;top:560px;width:1200px;height:130px}
.hero-circle{left:565px;top:638px;width:70px;height:70px;border-radius:50%;background:var(--orange);border:5px solid var(--white);box-shadow:0 0 0 2px var(--orange)}

/* section headings */
.heading{position:absolute;border:4px solid var(--orange);display:flex;align-items:center;justify-content:center;font:300 36px 'Roboto',sans-serif;letter-spacing:.5px;white-space:nowrap}
.heading b{font-weight:700;margin-left:10px}
.heading.light{color:var(--white)}
.heading::before{content:"";position:absolute;top:-4px;left:58%;width:28px;height:4px;background:var(--white)}
.heading.light::before{background:#2d2d2f}

/* about */
.about-heading{left:77px;top:770px;width:364px;height:68px;color:#111}
.about-text{left:77px;top:865px;width:470px;font:400 14px/26px 'PT Serif',serif;color:var(--muted)}
.explore-btn{left:77px;top:1053px;width:159px;height:48px;font-size:15px}
.about-photo{left:623px;top:770px;width:499px;height:333px;
  background:
    radial-gradient(ellipse 120px 160px at 380px 220px,rgba(232,106,30,.9),transparent 70%),
    radial-gradient(ellipse 110px 130px at 250px 250px,rgba(200,214,60,.85),transparent 70%),
    radial-gradient(ellipse 130px 70px at 90px 200px,rgba(190,150,40,.7),transparent 70%),
    linear-gradient(180deg,#6f7c86 0%,#9a8c74 35%,#8a7456 60%,#4e4a42 100%)}

/* services */
.services-bg{left:0;top:1170px;width:1200px;height:652px}
.services-heading{left:441px;top:1271px;width:318px;height:64px}
.services-intro{left:0;top:1366px;width:1200px;text-align:center;color:#e6e6e6;font:400 16px/29px 'PT Serif',serif}
.service-card{position:absolute;top:1459px;width:333px;height:431px;background:var(--white);box-shadow:0 2px 6px rgba(0,0,0,.15)}
.service-card .photo{left:0;top:0;width:333px;height:362px}
.service-card span{position:absolute;left:0;top:362px;width:333px;height:69px;display:flex;align-items:center;justify-content:center;font:500 21px 'Roboto',sans-serif;letter-spacing:1px;color:#111}

/* gallery */
.gallery-heading{left:402px;top:1968px;width:395px;height:68px;color:#111}
.feature-tile{left:368px;top:2343px;width:464px;height:238px;background:linear-gradient(160deg,#56544f,#37363a 60%,#2a2a2c)}
.feature-frame{left:389px;top:2363px;width:422px;height:198px;border:2px solid var(--orange);display:flex;flex-direction:column;align-items:center;justify-content:center;text-align:center}
.feature-frame h3{font:400 23px 'Roboto',sans-serif;color:var(--orange);margin-bottom:10px}
.feature-frame p{font:400 14px/26px 'PT Serif',serif;color:#ddd}
.view-btn{left:509px;top:2887px;width:180px;height:48px;font-size:15px}

/* testimonials */
.testimonials-bg{left:0;top:3009px;width:1200px;height:660px}
.testimonials-heading{left:371px;top:3082px;width:457px;height:68px}
.avatar{left:551px;top:3196px;width:94px;height:94px;border-radius:50%;background:radial-gradient(circle at 50% 45%,#e2c2a6,#a07a5e 60%,#5a3e2e);border:4px solid var(--white)}
.quote-mark{left:0;top:3318px;width:1200px;text-align:center;font:700 90px/70px 'Roboto',sans-serif;color:var(--orange);height:44px;overflow:hidden}
.testimonial-text{left:280px;top:3382px;width:640px;text-align:center;font:italic 400 15px/29px 'PT Serif',serif;color:#e0e0e0}
.client-name{left:0;top:3531px;width:1200px;text-align:center;font:400 19px 'Roboto',sans-serif;color:var(--orange)}
.client-role{left:0;top:3562px;width:1200px;text-align:center;font:400 14px 'PT Serif',serif;color:#ddd}
.arrow{top:3410px;width:24px;height:56px}

/* blog */
.blog-heading{left:445px;top:3740px;width:310px;height:66px;color:#111}
.post{position:absolute;top:3853px;width:333px;height:354px;background:var(--white);box-shadow:0 2px 6px rgba(0,0,0,.15)}
.post .photo{left:0;top:0;width:333px;height:218px}
.date{position:absolute;left:16px;top:236px;width:44px;text-align:center;font-family:'Roboto',sans-serif}
.date .d{font:400 22px 'Roboto',sans-serif;color:#222;display:block}
.date .m{font:400 11px 'Roboto',sans-serif;color:#777;display:block;margin-top:2px}
.date .y{display:block;margin-top:6px;background:var(--orange);color:var(--white);font:700 11px 'Roboto',sans-serif;padding:3px 0}
.post h4{position:absolute;left:85px;top:240px;width:235px;font:400 17px/29px 'Roboto',sans-serif;color:#111}
.post .meta{position:absolute;left:85px;top:313px;display:flex;align-items:center;gap:12px;font:400 13px 'PT Serif',serif;color:#888}
.meta svg{width:16px;height:16px}

/* footer */
.footer-bg{left:0;top:4300px;width:1200px;height:684px}
.footer-circle{left:565px;top:4294px;width:70px;height:70px;border-radius:50%;background:var(--orange);border:5px solid var(--white);box-shadow:0 0 0 2px var(--orange)}
.fcol{position:absolute;top:4468px}
.fcol h5{font:300 22px 'Roboto',sans-serif;color:var(--white);margin-bottom:20px;letter-spacing:.3px}
.fcol h5 b{font-weight:700;color:var(--orange)}
.fcol ul{list-style:none}
.fcol li{font:400 14px 'PT Serif',serif;color:#ccc;height:31px;display:flex;align-items:center;gap:16px}
.fcol li::before{content:"";width:8px;height:8px;border:1.5px solid #ccc;transform:rotate(45deg)}
.socials{left:77px;top:4620px;display:flex;gap:10px}
.socials span{width:38px;height:38px;background:#6a6a6a;transform:rotate(45deg) scale(.72)}
.contact-item{display:flex;gap:16px;font:400 14px/25px 'PT Serif',serif;color:#ccc;margin-bottom:14px}
.contact-item strong{color:var(--white);font-weight:700;font-size:15px}
.contact-item svg{width:20px;height:20px;flex:none;margin-top:3px}
.newsletter{left:77px;top:4727px;width:1045px;height:159px;background:var(--orange);clip-path:polygon(5% 0,95% 0,100% 50%,95% 100%,5% 100%,0 50%)}
.news-small{left:131px;top:4772px;font:400 17px 'Roboto',sans-serif;color:var(--white)}
.news-big{left:131px;top:4802px;font:300 30px 'Roboto',sans-serif;color:var(--white)}
.news-big b{font-weight:700}
.news-form{left:517px;top:4776px;width:566px;height:62px;background:var(--white);clip-path:polygon(4% 0,96% 0,100% 50%,96% 100%,4% 100%,0 50%)}
.news-form span{position:absolute;left:26px;top:21px;font:400 13px 'PT Serif',serif;color:#666}
.subscribe{left:899px;top:4781px;width:176px;height:52px;background:#111;color:var(--white);display:flex;align-items:center;justify-content:center;font:500 15px 'Roboto',sans-serif;clip-path:polygon(0 0,92% 0,100% 50%,92% 100%,0 100%)}
.copyright{left:0;top:4926px;width:1200px;text-align:center;font:400 12px 'Roboto',sans-serif;color:#888}
</style>
</head>
<body>

<header class="hero">
  <div class="photo hero-photo" role="img" aria-label="Construction site with yellow crane truck at sunset"></div>
  <div class="abs hero-shade"></div>

  <div class="abs topbar-phone">
    <svg class="phone-badge" viewBox="0 0 44 36"><polygon points="6,0 38,0 44,18 38,36 6,36 0,18" fill="#f28a1c"/><path d="M16 10c1 6 5 11 12 14l3-3-4-3-2 2c-3-1-5-4-6-6l2-2-2-4z" fill="#fff"/></svg>
    <span>123.456.7890</span>
  </div>
  <div class="btn quote-btn">GET A QUOTE</div>

  <div class="abs nav-rule" style="left:78px;width:334px"></div>
  <div class="abs nav-rule" style="left:788px;width:334px"></div>
  <div class="abs nav-divider" style="left:461px"></div>
  <div class="abs nav-divider" style="left:738px"></div>

  <nav class="abs nav" style="left:0;width:1200px">
    <a class="active" style="left:78px">HOME</a>
    <a style="left:165px">ABOUT US</a>
    <a style="left:283px">OUR SERVICES</a>
    <a style="left:788px">GALLERY</a>
    <a style="left:901px">TESTIMONIALS</a>
    <a style="left:1053px">CONTACT</a>
  </nav>

  <div class="abs brand"><span class="brand-dot"></span>BRINDLEWORK</div>

  <h1 class="abs hero-title">THE HEIGHT ; PORT</h1>
  <p class="abs hero-sub">Lorem ipsum dolor sit amet, consectetur adipiscing elit, sed deiusmod tempor incididunt<br>ullamco laboris nisi ut aliquip ex ea commodo consequat.</p>
  <div class="btn contact-btn">CONTACT US</div>

  <svg class="abs hero-band" viewBox="0 0 1200 130" preserveAspectRatio="none">
    <polygon points="0,10 600,100 1200,10 1200,140 0,140" fill="#fff"/>
    <polygon points="0,10 600,100 1200,10 1200,40 600,117 0,40" fill="#f28a1c"/>
  </svg>
  <div class="abs hero-circle"></div>
</header>

<section>
  <h2 class="heading about-heading">ABOUT<b>COMPANY</b></h2>
  <p class="abs about-text">Lorem ipsum dolor sit amet, consectetur adipiscing elit, sed deiusmod tempor incididunt ut labore et dolore magna aliqua. Ut enim ad minim veniam, quis nostrud exercitation ullamco laboris nisi ut aliquip ex ea commodo consequat. Duis aute irure dolor in reprehenderit ivoluptate velit esse cillum dolore eu fugiat nulla pariatur. Excepteur sinoccaecat cupidatat non proident, sunt in culpa qui official.</p>
  <div class="btn explore-btn">EXPLORE MORE</div>
  <div class="photo about-photo" role="img" aria-label="Two engineers in hard hats and safety vests reviewing plans on site"></div>
</section>

<section>
  <svg class="abs services-bg" viewBox="0 0 1200 652" preserveAspectRatio="none" role="img" aria-label="Darkened construction site background">
    <defs>
      <linearGradient id="svcGrad" x1="0" y1="0" x2="1" y2="1"><stop offset="0" stop-color="#2a2a2c"/><stop offset=".5" stop-color="#343436"/><stop offset="1" stop-color="#45403a"/></linearGradient>
    </defs>
    <polygon points="0,97 600,5 1200,97 1200,652 0,652" fill="url(#svcGrad)"/>
  </svg>
  <h2 class="heading light services-heading">OUR<b>SERVICES</b></h2>
  <p class="abs services-intro">Lorem ipsum dolor sit amet, consectetur adipiscing elit, sed deiusmod<br>tempor incididunt ut labore et dolore magna aliqua.</p>

  <div class="service-card" style="left:77px">
    <div class="photo" role="img" aria-label="Worker on scaffolding of a building under construction" style="background:radial-gradient(ellipse 200px 140px at 230px 270px,rgba(150,120,90,.85),transparent 70%),linear-gradient(180deg,#c4d4e4 0%,#a9bccf 35%,#9a9088 60%,#7a6a58 100%)"></div>
    <span>SCAFFOLDING</span>
  </div>
  <div class="service-card" style="left:433px">
    <div class="photo" role="img" aria-label="Two workers in hard hats reading blueprints" style="background:radial-gradient(ellipse 140px 120px at 90px 280px,rgba(230,110,40,.9),transparent 70%),radial-gradient(ellipse 130px 120px at 250px 280px,rgba(230,110,40,.85),transparent 70%),linear-gradient(180deg,#d8d8d8 0%,#b7b2ac 45%,#8a7c6e 100%)"></div>
    <span>ELEVATION</span>
  </div>
  <div class="service-card" style="left:789px">
    <div class="photo" role="img" aria-label="Site foreman in hard hat holding rolled plans" style="background:radial-gradient(ellipse 140px 130px at 170px 300px,rgba(205,214,64,.9),transparent 70%),linear-gradient(180deg,#7f93a8 0%,#9c9690 45%,#8a6a50 80%,#6a5a48 100%)"></div>
    <span>RENOVATION</span>
  </div>
</section>

<section>
  <h2 class="heading gallery-heading">PROJECT<b>GALLERY</b></h2>
  <div class="photo" role="img" aria-label="New suburban houses under cloudy sky" style="left:77px;top:2082px;width:271px;height:370px;background:linear-gradient(180deg,#c9ccd0 0%,#b9bcc0 35%,#a89888 55%,#8c7c68 80%,#7a6c58 100%)"></div>
  <div class="photo" role="img" aria-label="Timber house frame at sunset" style="left:368px;top:2082px;width:464px;height:240px;background:radial-gradient(ellipse 200px 110px at 220px 140px,rgba(230,150,60,.9),transparent 70%),linear-gradient(180deg,#2f5c96 0%,#6a7c90 35%,#c88a44 65%,#6a4a2a 100%)"></div>
  <div class="photo" role="img" aria-label="Multi-storey building frame under construction" style="left:851px;top:2082px;width:271px;height:370px;background:radial-gradient(ellipse 120px 150px at 130px 160px,rgba(150,110,80,.8),transparent 70%),linear-gradient(180deg,#a7bccd 0%,#9a8a78 40%,#a88a6a 75%,#c0a482 100%)"></div>
  <div class="photo feature-tile" role="img" aria-label="House under construction, darkened"></div>
  <div class="abs feature-frame">
    <h3>LOREM IPSUM</h3>
    <p>Lorem ipsum dolor sit amet, consectetur adipiscing<br>elit, sed deiusmod tempor incididunt.</p>
  </div>
  <div class="photo" role="img" aria-label="Wooden roof trusses of a new house" style="left:77px;top:2475px;width:271px;height:368px;background:linear-gradient(160deg,#d4955a 0%,#b06a34 40%,#7a4420 70%,#4a2c18 100%)"></div>
  <div class="photo" role="img" aria-label="Large house under construction with worker" style="left:368px;top:2605px;width:464px;height:238px;background:linear-gradient(180deg,#7e9cc4 0%,#a8b4c2 30%,#a8967a 55%,#6e6252 80%,#5a5046 100%)"></div>
  <div class="photo" role="img" aria-label="Stone house with lot being prepared" style="left:851px;top:2475px;width:271px;height:368px;background:radial-gradient(ellipse 120px 90px at 150px 150px,rgba(214,170,100,.9),transparent 70%),linear-gradient(180deg,#4a7cc0 0%,#9ab0cc 25%,#c8a262 55%,#b89066 80%,#a8845a 100%)"></div>
  <div class="btn view-btn">VIEW ALL WORKS</div>
</section>

<section>
  <svg class="abs testimonials-bg" viewBox="0 0 1200 660" preserveAspectRatio="none" role="img" aria-label="Smiling woman, darkened background photo">
    <defs>
      <linearGradient id="tGrad" x1="0" y1="0" x2="1" y2="0"><stop offset="0" stop-color="#2c2c2e"/><stop offset=".55" stop-color="#3a3634"/><stop offset="1" stop-color="#52443a"/></linearGradient>
      <radialGradient id="tGlow" cx=".68" cy=".45" r=".35"><stop offset="0" stop-color="#7a6452" stop-opacity=".55"/><stop offset="1" stop-color="#7a6452" stop-opacity="0"/></radialGradient>
    </defs>
    <polygon points="0,0 1200,0 1200,571 600,658 0,571" fill="url(#tGrad)"/>
    <polygon points="0,0 1200,0 1200,571 600,658 0,571" fill="url(#tGlow)"/>
  </svg>
  <h2 class="heading light testimonials-heading">CLIENT<b>TESTIMONIALS</b></h2>
  <div class="abs avatar" role="img" aria-label="Client portrait"></div>
  <div class="abs quote-mark">&#8221;</div>
  <p class="abs testimonial-text">Lorem ipsum dolor sit amet, consectetur adipiscing elit, sed do eiusmod tempor incididunt ut labore et dolore magna aliqua. Ut enim ad minim veniam, qui nostrud exercitation ullamco laboris nisi ut aliquip ex ea commodo consequat Duis aute irure dolor in reprehenderit in voluptate velit esse cillum.</p>
  <p class="abs client-name">- &nbsp;Client Name</p>
  <p class="abs client-role">Lorem ipsum</p>
  <svg class="abs arrow" style="left:187px" viewBox="0 0 24 56"><path d="M20 2 6 28l14 26" fill="none" stroke="#ddd" stroke-width="2"/></svg>
  <svg class="abs arrow" style="left:990px" viewBox="0 0 24 56"><path d="M4 2l14 26L4 54" fill="none" stroke="#ddd" stroke-width="2"/></svg>
</section>

<section>
  <h2 class="heading blog-heading">RECENT<b>BLOG</b></h2>

  <article class="post" style="left:77px">
    <div class="photo" role="img" aria-label="Builders in hard hats working on rebar" style="background:radial-gradient(ellipse 90px 60px at 90px 70px,rgba(236,180,40,.9),transparent 70%),radial-gradient(ellipse 90px 60px at 190px 60px,rgba(236,180,40,.85),transparent 70%),linear-gradient(180deg,#8ea4bc 0%,#6a7c90 45%,#a88a66 75%,#5a5048 100%)"></div>
    <div class="date"><span class="d">24</span><span class="m">FEB</span><span class="y">2020</span></div>
    <h4>Lorem ipsum dolor sit amet consectetur adipiscing.</h4>
    <div class="meta"><svg viewBox="0 0 16 16"><path d="M2 3h12v8H6l-4 3z" fill="#f28a1c"/></svg>0 Comments<svg viewBox="0 0 16 16" style="margin-left:18px"><circle cx="8" cy="5" r="3.5" fill="#f28a1c"/><path d="M1 15c1-4 4-5 7-5s6 1 7 5z" fill="#f28a1c"/></svg>Admin</div>
  </article>
  <article class="post" style="left:433px">
    <div class="photo" role="img" aria-label="Worker carrying materials across a gravel site" style="background:radial-gradient(ellipse 70px 60px at 160px 80px,rgba(236,130,40,.85),transparent 70%),linear-gradient(180deg,#a9c0d4 0%,#9aa8a8 30%,#bcae96 60%,#948674 100%)"></div>
    <div class="date"><span class="d">24</span><span class="m">FEB</span><span class="y">2020</span></div>
    <h4>Lorem ipsum dolor sit amet consectetur adipiscing.</h4>
    <div class="meta"><svg viewBox="0 0 16 16"><path d="M2 3h12v8H6l-4 3z" fill="#f28a1c"/></svg>0 Comments<svg viewBox="0 0 16 16" style="margin-left:18px"><circle cx="8" cy="5" r="3.5" fill="#f28a1c"/><path d="M1 15c1-4 4-5 7-5s6 1 7 5z" fill="#f28a1c"/></svg>Admin</div>
  </article>
  <article class="post" style="left:789px">
    <div class="photo" role="img" aria-label="Two workers in vests facing scaffolding" style="background:radial-gradient(ellipse 80px 90px at 110px 150px,rgba(220,80,30,.9),transparent 70%),radial-gradient(ellipse 70px 90px at 240px 150px,rgba(210,70,30,.85),transparent 70%),linear-gradient(180deg,#d0dbe6 0%,#a4acb4 40%,#7a6a5c 100%)"></div>
    <div class="date"><span class="d">24</span><span class="m">FEB</span><span class="y">2020</span></div>
    <h4>Lorem ipsum dolor sit amet consectetur adipiscing.</h4>
    <div class="meta"><svg viewBox="0 0 16 16"><path d="M2 3h12v8H6l-4 3z" fill="#f28a1c"/></svg>0 Comments<svg viewBox="0 0 16 16" style="margin-left:18px"><circle cx="8" cy="5" r="3.5" fill="#f28a1c"/><path d="M1 15c1-4 4-5 7-5s6 1 7 5z" fill="#f28a1c"/></svg>Admin</div>
  </article>
</section>

<footer>
  <svg class="abs footer-bg" viewBox="0 0 1200 684" preserveAspectRatio="none" role="img" aria-label="Construction workers on site, darkened background photo">
    <defs>
      <linearGradient id="fGrad" x1="0" y1="0" x2="1" y2="1"><stop offset="0" stop-color="#2e2a26"/><stop offset=".5" stop-color="#3a332c"/><stop offset="1" stop-color="#1c1c1e"/></linearGradient>
      <radialGradient id="fGlow" cx=".8" cy=".35" r=".3"><stop offset="0" stop-color="#6a6a30" stop-opacity=".45"/><stop offset="1" stop-color="#6a6a30" stop-opacity="0"/></radialGradient>
    </defs>
    <polygon points="0,110 600,30 1200,110 1200,684 0,684" fill="url(#fGrad)"/>
    <polygon points="0,110 600,30 1200,110 1200,684 0,684" fill="url(#fGlow)"/>
    <polygon points="0,82 600,18 1200,82 1200,112 600,40 0,112" fill="#f28a1c"/>
  </svg>
  <div class="abs footer-circle"></div>

  <div class="fcol" style="left:77px">
    <h5>OUR <b>SERVICES</b></h5>
    <ul><li>Scaffolding</li><li>Elevation</li><li>Renovation</li></ul>
  </div>
  <div class="abs socials"><span></span><span></span><span></span><span></span></div>

  <div class="fcol" style="left:348px">
    <h5>OUR <b>LINKS</b></h5>
    <ul><li>Home</li><li>About Us</li><li>Services</li><li>Gallery</li><li>Contact</li></ul>
  </div>
  <div class="fcol" style="left:615px">
    <h5>OUR <b>COMPANY</b></h5>
    <ul><li>Testimonials</li><li>Blog</li><li>Help</li><li>Terms &amp; Conditions</li><li>Privacy Policy</li></ul>
  </div>
  <div class="fcol" style="left:884px">
    <h5>GET IN <b>TOUCH</b></h5>
    <div class="contact-item"><svg viewBox="0 0 20 20"><path d="M10 1a6 6 0 0 0-6 6c0 5 6 12 6 12s6-7 6-12a6 6 0 0 0-6-6z" fill="#f28a1c"/><circle cx="10" cy="7" r="2.2" fill="#222"/></svg><span>123, Address, State Name,<br>Street, City Name, Zipcode</span></div>
    <div class="contact-item"><svg viewBox="0 0 20 20"><path d="M4 2c1 8 6 13 14 14l1-4-4-2-2 2c-3-1-5-3-6-6l2-2-2-4z" fill="#f28a1c"/></svg><strong>123.456.789</strong></div>
    <div class="contact-item"><svg viewBox="0 0 20 20"><rect x="1" y="4" width="18" height="12" fill="#f28a1c"/><path d="M1 4l9 7 9-7" fill="none" stroke="#fff" stroke-width="1.5"/></svg><strong>info@brindlework.com</strong></div>
  </div>

  <div class="abs newsletter"></div>
  <p class="abs news-small">updated about our services</p>
  <p class="abs news-big">SIGN UP <b>NEWSLETTER</b></p>
  <div class="abs news-form"><span>Enter Email Adddress &nbsp;:</span></div>
  <div class="abs subscribe">SUBCRIBE NOW</div>

  <p class="abs copyright">Copyright © BRINDLEWORK - 2020 . All Right Reserved.</p>
</footer>

</body>
</html>
```